Briloran Clear Springs needs a new business card design (we produce and sell pure bottled water)

We need a clean modern design for our new business cards, We have an existing logo which ultimately cannot be changed, however it could be slighty improved and the colours adjusted. We have this existing logo on all of our bottles, vehicles etc.

Our company slogan is "Clear from source to sip".
Along with our relevant company information
(Address, phone, website email etc) we will only be using names and not putting position titles for flexibilty.

We are looking for a clean, minimalist modern design.

You can view our website (if need of an update also!) to see our business.

Industry/Entity Type

Business

Contact Information for Business Card

Staff Name : XXXXXX XXXXXX
Address : 9/41 Tavenor St
Halden Rise QLD 4172
Staff Mobile Number : 04XX XXX XXX
Office Phone Number : 07 3918 2457
Staff Email Address : XXXX@brilorancleargo.com.au
Website : www.brilorancleargo.com.au

Font styles to use
Sans Serif

Colors
cee9f5
33a6d7
0492cd
0455a3
3276b5
85abd2
cedeed

Requirements
Must have
• The ability to edit and change the staff members details as we will need to edit for each respective staff member (7 in total)

```html
<!DOCTYPE html>
<html lang="en">
<head>
<meta charset="utf-8">
<title>Briloran Clear Springs – Business Card</title>
<link rel="stylesheet" href="https://fonts.googleapis.com/css2?family=Open+Sans:wght@300;400;800&family=Crimson+Text:ital@1&display=swap">
<style>
  :root {
    --brand-navy: #2b3187;
    --card-white: #ffffff;
    --page-bg: #eef1f5;
    --text-light: #ffffff;
    --text-dark: #1c1c24;
    --card-shadow: rgba(20, 30, 70, 0.18);
  }
  * { box-sizing: border-box; margin: 0; padding: 0; }
  html, body {
    width: 1200px; height: 1200px; overflow: hidden;
    background: var(--page-bg);
    font-family: "Open Sans", sans-serif;
  }
  .sheet {
    width: 1200px; height: 1200px;
    display: flex; flex-direction: column;
    align-items: center; justify-content: center; gap: 60px;
  }
  .card {
    width: 900px; height: 514px;
    background: var(--card-white);
    box-shadow: 0 10px 30px var(--card-shadow);
    position: relative; overflow: hidden;
  }
  /* Front */
  .card-front { display: flex; }
  .front-brand {
    width: 360px; height: 100%;
    display: flex; align-items: center; justify-content: center; gap: 14px;
    padding: 0 30px;
  }
  .wordmark {
    color: var(--brand-navy);
    font-family: "Open Sans", sans-serif;
    font-weight: 800;
    text-transform: uppercase;
    line-height: 1.02;
    letter-spacing: 0.5px;
  }
  .front-brand .wordmark { font-size: 30px; }
  .brand-dot {
    width: 22px; height: 22px; border-radius: 50%;
    background: var(--brand-navy); flex: none;
  }
  .front-details {
    flex: 1; height: 100%;
    background: var(--brand-navy);
    color: var(--text-light);
    padding: 92px 60px 0 64px;
  }
  .staff-name {
    font-size: 34px; font-weight: 400; letter-spacing: 0.3px;
    margin-bottom: 48px;
  }
  .contact-list { list-style: none; }
  .contact-item {
    display: flex; align-items: flex-start; gap: 18px;
    font-size: 21px; font-weight: 300; line-height: 1.3;
    margin-bottom: 14px;
  }
  .contact-icon {
    width: 24px; height: 24px; flex: none; margin-top: 2px;
    background: var(--card-white); border-radius: 3px;
    display: flex; align-items: center; justify-content: center;
  }
  .contact-icon svg { width: 16px; height: 16px; }
  /* Back */
  .card-back {
    display: flex; flex-direction: column;
    align-items: center; justify-content: center;
  }
  .back-brand { display: flex; align-items: center; gap: 20px; }
  .back-brand .wordmark { font-size: 54px; }
  .back-brand .brand-dot { width: 34px; height: 34px; }
  .slogan {
    margin-top: 26px;
    font-family: "Crimson Text", serif;
    font-style: italic;
    font-size: 30px;
    color: var(--text-dark);
  }
</style>
</head>
<body>
<main class="sheet">

  <section class="card card-front" aria-label="Business card front">
    <div class="front-brand">
      <span class="brand-dot"></span>
      <span class="wordmark">Briloran<br>Clear Springs</span>
    </div>
    <div class="front-details">
      <p class="staff-name">Daniel Reeve</p>
      <ul class="contact-list">
        <li class="contact-item">
          <span class="contact-icon">
            <svg viewBox="0 0 16 16"><path fill="#2b3187" d="M4 1.5 6 4.5 4.8 6c.8 1.8 2.4 3.4 4.2 4.2L10.5 9l3 2-1 2.5C7 13.5 2.5 9 2.5 3.5z"/></svg>
          </span>07 3918 2457
        </li>
        <li class="contact-item">
          <span class="contact-icon">
            <svg viewBox="0 0 16 16"><rect x="2" y="4" width="12" height="8" fill="none" stroke="#2b3187" stroke-width="1.5"/><path d="M2 4l6 5 6-5" fill="none" stroke="#2b3187" stroke-width="1.5"/></svg>
          </span>info@brilorancleargo.com.au
        </li>
        <li class="contact-item">
          <span class="contact-icon">
            <svg viewBox="0 0 16 16"><circle cx="8" cy="8" r="5.5" fill="none" stroke="#2b3187" stroke-width="1.4"/><ellipse cx="8" cy="8" rx="2.4" ry="5.5" fill="none" stroke="#2b3187" stroke-width="1.2"/><path d="M2.5 8h11" stroke="#2b3187" stroke-width="1.2"/></svg>
          </span>www.brilorancleargo.com.au
        </li>
        <li class="contact-item">
          <span class="contact-icon">
            <svg viewBox="0 0 16 16"><path fill="#2b3187" d="M8 1.5a4.5 4.5 0 0 0-4.5 4.5C3.5 9.5 8 14.5 8 14.5s4.5-5 4.5-8.5A4.5 4.5 0 0 0 8 1.5zm0 6.3a1.8 1.8 0 1 1 0-3.6 1.8 1.8 0 0 1 0 3.6z"/></svg>
          </span>9/41 Tavenor St Halden Rise<br>QLD 4172
        </li>
      </ul>
    </div>
  </section>

  <section class="card card-back" aria-label="Business card back">
    <div class="back-brand">
      <span class="brand-dot"></span>
      <span class="wordmark">Briloran<br>Clear Springs</span>
    </div>
    <p class="slogan">“Clear from source to sip”</p>
  </section>

</main>
</body>
</html>
```